TALMORK

The business want a professional looking business card. We have a scetch we will add but want the extra upgrade, and would like more suggestions for variations of our business cards.

```html
<!DOCTYPE html>
<html lang="en">
<head>
<meta charset="utf-8">
<title>TALMORK – Business Card</title>
<link href="https://fonts.googleapis.com/css2?family=Mulish:wght@400;600;700&display=swap" rel="stylesheet">
<style>
  :root {
    --backdrop: #5e5e5e;
    --card-white: #ffffff;
    --gold: #e3a63f;
    --gold-light: #f9cf6e;
    --gold-deep: #d7983a;
    --ink: #3d3d3d;
    --ink-soft: #666666;
  }
  * { margin: 0; padding: 0; box-sizing: border-box; }
  html, body { width: 1123px; height: 1200px; overflow: hidden; }
  body {
    background: var(--backdrop);
    font-family: "Mulish", sans-serif;
    position: relative;
  }
  .card {
    position: absolute;
    left: 131px;
    width: 860px;
    height: 528px;
    border-radius: 28px;
    overflow: hidden;
  }
  .card--front { top: 48px; background: var(--card-white); }
  .card--back {
    top: 624px;
    background: radial-gradient(ellipse at 45% 20%, var(--gold-light) 0%, #efbb57 45%, var(--gold-deep) 100%);
  }
  .front-band {
    position: absolute;
    left: 0; right: 0; bottom: 0;
    height: 118px;
    background: linear-gradient(90deg, #e8ae4c 0%, var(--gold-light) 50%, #dea046 100%);
  }

  .brand {
    position: absolute;
    left: 55px;
    top: 150px;
    width: 280px;
    text-align: center;
  }
  .brand__dot {
    display: block;
    width: 70px; height: 70px;
    margin: 0 auto 22px;
    border-radius: 50%;
    background: var(--gold);
  }
  .brand__name {
    font-size: 44px;
    font-weight: 700;
    letter-spacing: 3px;
    color: var(--gold);
    line-height: 1;
  }
  .brand__since {
    margin-top: 8px;
    font-size: 20px;
    letter-spacing: 3px;
    color: var(--ink-soft);
  }

  .person {
    position: absolute;
    left: 489px;
    top: 128px;
    line-height: 33px;
    font-size: 27px;
    color: var(--ink);
  }
  .person__name { color: var(--gold); font-weight: 700; letter-spacing: 0.5px; }

  .contacts {
    position: absolute;
    left: 455px;
    top: 264px;
    list-style: none;
    font-size: 26px;
    color: var(--ink);
  }
  .contacts li { display: flex; align-items: center; height: 40px; }
  .contacts svg { width: 20px; height: 20px; margin-right: 14px; fill: var(--ink); }

  .back-mark {
    position: absolute;
    left: 0; top: 0; width: 100%; height: 100%;
    display: flex; flex-direction: column; align-items: center; justify-content: center;
  }
  .back-mark__dot {
    width: 96px; height: 96px; border-radius: 50%;
    background: var(--card-white);
    margin-bottom: 26px;
  }
  .back-mark__name {
    font-size: 64px; font-weight: 700; letter-spacing: 5px;
    color: var(--card-white);
    line-height: 1;
  }
</style>
</head>
<body>

<section class="card card--front">
  <div class="front-band" role="img" aria-label="Decorative gold and dark swoosh band along the lower edge"></div>

  <div class="brand">
    <span class="brand__dot"></span>
    <div class="brand__name">TALMORK</div>
    <div class="brand__since">SINCE 2026</div>
  </div>

  <div class="person">
    <div class="person__name">TALMORK E SANDVIK</div>
    <div class="person__role">CEO &amp; Founder</div>
    <div class="person__full">Eirik Holm Sandvik</div>
  </div>

  <ul class="contacts">
    <li>
      <svg viewBox="0 0 24 24" aria-label="Phone"><path d="M6.6 10.8a15.1 15.1 0 0 0 6.6 6.6l2.2-2.2c.3-.3.7-.4 1-.2 1.1.4 2.3.6 3.6.6.6 0 1 .4 1 1V20c0 .6-.4 1-1 1A17 17 0 0 1 3 4c0-.6.4-1 1-1h3.5c.6 0 1 .4 1 1 0 1.3.2 2.5.6 3.6.1.3 0 .7-.2 1z"/></svg>
      <span>004790215574</span>
    </li>
    <li>
      <svg viewBox="0 0 24 24" aria-label="Email"><path d="M2 5h20v14H2z M3 6.5v.6l9 6 9-6v-.6z" fill-rule="evenodd"/></svg>
      <span>talmork.llc@mailbox.no</span>
    </li>
    <li>
      <svg viewBox="0 0 24 24" aria-label="Website"><path d="M12 2a10 10 0 1 0 0 20 10 10 0 0 0 0-20zm6.9 6h-3a15 15 0 0 0-1.3-3.9A8 8 0 0 1 18.9 8zM12 4c.8 1.1 1.5 2.5 1.9 4h-3.8c.4-1.5 1.1-2.9 1.9-4zM4.3 14a8 8 0 0 1 0-4h3.4a16 16 0 0 0 0 4zm.8 2h3a15 15 0 0 0 1.3 3.9A8 8 0 0 1 5.1 16zm3-8h-3a8 8 0 0 1 4.3-3.9C8.9 5.3 8.4 6.6 8.1 8zM12 20c-.8-1.1-1.5-2.5-1.9-4h3.8c-.4 1.5-1.1 2.9-1.9 4zm2.3-6H9.7a14 14 0 0 1 0-4h4.6a14 14 0 0 1 0 4zm.3 5.9c.6-1.2 1-2.5 1.300-3.9h3a8 8 0 0 1-4.3 3.9zm1.7-5.9a16 16 0 0 0 0-4h3.4a8 8 0 0 1 0 4z"/></svg>
      <span>www.talmork.llc</span>
    </li>
  </ul>
</section>

<section class="card card--back">
  <div class="back-mark">
    <span class="back-mark__dot"></span>
    <div class="back-mark__name">TALMORK</div>
  </div>
</section>

</body>
</html>
```